Growth - Measuring KPI

Hello -
You made this graphic for me a few months ago. I would like your help to create another one.
Duplicate the "growth gear"
Have 3 light bulbs surrounding the gear. One on top (shouldnt be lit up, not connecting), 2nd should be 1/3 of the way around the gear and should be half lit up, the 3rd should be 2/3 of the way around the gear and fully lit up. Have narrow arrows connecting the light bulbs. In between the 2nd and 3rd light bulb needs to be a small bar graph. See photos attached.

Logo Text

No words just images.

```html
<!DOCTYPE html>
<html lang="en">
<head>
<meta charset="utf-8">
<title>Growth – Measuring KPI</title>
<style>
  :root {
    --ink: #231f20;
    --paper: #ffffff;
    --lit: #fdca00;
    --bar-light: #d1d3d6;
    --bar-mid: #58595b;
    --trend: #13214f;
    --tree-tone: #2e2a2b;
  }
  html, body {
    margin: 0;
    padding: 0;
    width: 1200px;
    height: 1200px;
    overflow: hidden;
    background: var(--paper);
  }
  .growth-cycle {
    display: block;
    width: 1200px;
    height: 1200px;
  }
  .cycle-arrow { fill: none; stroke: var(--ink); stroke-width: 6; }
  .arrow-head { fill: var(--ink); }
  .gear-body { fill: var(--ink); }
  .gear-hole { fill: var(--paper); }
  .tree-area { fill: var(--tree-tone); }
  .bulb-outline { fill: none; stroke: var(--ink); stroke-width: 10; stroke-linejoin: round; }
  .bulb-glass-lit { fill: var(--lit); }
  .bulb-base { fill: none; stroke: var(--ink); stroke-width: 10; stroke-linecap: round; }
  .bulb-cap { fill: var(--ink); }
  .bulb-rays { stroke: var(--ink); stroke-width: 5; stroke-linecap: round; }
  .bulb-rays--lit { stroke: var(--lit); }
  .bulb-shine { fill: none; stroke: var(--ink); stroke-width: 9; stroke-linecap: round; }
  .bulb-shine--lit { stroke: var(--paper); }
  .bar--light { fill: var(--bar-light); }
  .bar--mid { fill: var(--bar-mid); }
  .bar--dark { fill: var(--ink); }
  .chart-axis { stroke: var(--ink); stroke-width: 2; }
  .trend-line { fill: none; stroke: var(--trend); stroke-width: 8; }
  .trend-head { fill: var(--trend); }
</style>
</head>
<body>
<svg class="growth-cycle" viewBox="0 0 1920 1920" xmlns="http://www.w3.org/2000/svg" role="img" aria-label="Growth gear surrounded by three light bulbs joined by arrows, with a rising bar chart">
  <defs>
    <marker id="arrowhead" viewBox="0 0 10 10" refX="2" refY="5" markerWidth="9" markerHeight="9" orient="auto" markerUnits="strokeWidth">
      <path class="arrow-head" d="M0,0 L10,5 L0,10 L2,5 Z"/>
    </marker>
    <g id="bulb-rays">
      <line x1="0" y1="-100" x2="0" y2="-118"/>
      <line x1="38" y1="-92" x2="45" y2="-109"/>
      <line x1="71" y1="-71" x2="83" y2="-83"/>
      <line x1="92" y1="-38" x2="109" y2="-45"/>
      <line x1="100" y1="0" x2="118" y2="0"/>
      <line x1="92" y1="38" x2="109" y2="45"/>
      <line x1="71" y1="71" x2="83" y2="83"/>
      <line x1="-38" y1="-92" x2="-45" y2="-109"/>
      <line x1="-71" y1="-71" x2="-83" y2="-83"/>
      <line x1="-92" y1="-38" x2="-109" y2="-45"/>
      <line x1="-100" y1="0" x2="-118" y2="0"/>
      <line x1="-92" y1="38" x2="-109" y2="45"/>
      <line x1="-71" y1="71" x2="-83" y2="83"/>
    </g>
    <path id="bulb-glass" d="M-35,116 C-38,70 -72,52 -72,0 A72 72 0 1 1 72 0 C72,52 38,70 35,116 Z"/>
    <g id="bulb-base">
      <line x1="-24" y1="136" x2="24" y2="136"/>
      <line x1="-24" y1="152" x2="24" y2="152"/>
    </g>
    <clipPath id="half-lit">
      <polygon points="1300,1000 1700,1000 1700,1245 1300,1160"/>
    </clipPath>
    <g id="gear-tooth">
      <polygon points="-35,0 35,0 52,62 -52,62"/>
    </g>
  </defs>

  <!-- Cycle arrows -->
  <path class="cycle-arrow" d="M482,1062 A490 490 0 0 1 808,602" marker-end="url(#arrowhead)"/>
  <path class="cycle-arrow" d="M1100,588 A490 490 0 0 1 1452,1008" marker-end="url(#arrowhead)"/>
  <path class="cycle-arrow" d="M1370,1348 A496 496 0 0 1 582,1342" marker-end="url(#arrowhead)"/>

  <!-- Growth gear -->
  <g class="growth-gear">
    <g class="gear-body">
      <circle cx="966" cy="1060" r="300"/>
      <use href="#gear-tooth" transform="translate(966,1060) rotate(0) translate(0,-348)"/>
      <use href="#gear-tooth" transform="translate(966,1060) rotate(45) translate(0,-348)"/>
      <use href="#gear-tooth" transform="translate(966,1060) rotate(90) translate(0,-348)"/>
      <use href="#gear-tooth" transform="translate(966,1060) rotate(135) translate(0,-348)"/>
      <use href="#gear-tooth" transform="translate(966,1060) rotate(180) translate(0,-348)"/>
      <use href="#gear-tooth" transform="translate(966,1060) rotate(225) translate(0,-348)"/>
      <use href="#gear-tooth" transform="translate(966,1060) rotate(270) translate(0,-348)"/>
      <use href="#gear-tooth" transform="translate(966,1060) rotate(315) translate(0,-348)"/>
    </g>
    <circle class="gear-hole" cx="966" cy="1060" r="232"/>
    <rect class="tree-area" x="842" y="880" width="266" height="365" rx="24" role="img" aria-label="Tree with hand-shaped branches and spreading roots"/>
  </g>

  <!-- Bulb 1: unlit, top -->
  <g class="bulb bulb--off" transform="translate(966,495)">
    <g class="bulb-rays"><use href="#bulb-rays"/></g>
    <use href="#bulb-glass" class="bulb-outline"/>
    <path class="bulb-shine" d="M-28,-38 Q-48,0 -22,40"/>
    <g class="bulb-base"><use href="#bulb-base"/></g>
    <path class="bulb-cap" d="M-14,164 A14 14 0 0 0 14,164 Z"/>
  </g>

  <!-- Bulb 2: half lit, right -->
  <g class="bulb bulb--half">
    <g clip-path="url(#half-lit)">
      <use href="#bulb-glass" class="bulb-glass-lit" transform="translate(1515,1215) rotate(102)"/>
    </g>
    <g transform="translate(1515,1215) rotate(102)">
      <g class="bulb-rays"><use href="#bulb-rays"/></g>
      <use href="#bulb-glass" class="bulb-outline"/>
      <g class="bulb-base"><use href="#bulb-base"/></g>
      <path class="bulb-cap" d="M-14,164 A14 14 0 0 0 14,164 Z"/>
    </g>
    <g class="bulb-rays bulb-rays--lit">
      <line x1="1455" y1="1120" x2="1463" y2="1133"/>
      <line x1="1495" y1="1105" x2="1498" y2="1120"/>
      <line x1="1540" y1="1105" x2="1536" y2="1120"/>
      <line x1="1580" y1="1123" x2="1571" y2="1135"/>
      <line x1="1610" y1="1153" x2="1597" y2="1161"/>
      <line x1="1626" y1="1195" x2="1611" y2="1198"/>
    </g>
  </g>

  <!-- Bulb 3: fully lit, left -->
  <g class="bulb bulb--on" transform="translate(416,1215) rotate(-100)">
    <g class="bulb-rays bulb-rays--lit"><use href="#bulb-rays"/></g>
    <use href="#bulb-glass" class="bulb-glass-lit"/>
    <path class="bulb-shine bulb-shine--lit" d="M-45,-30 Q-50,15 -20,42"/>
    <g class="bulb-base"><use href="#bulb-base"/></g>
    <path class="bulb-cap" d="M-14,164 A14 14 0 0 0 14,164 Z"/>
  </g>

  <!-- Growth bar chart -->
  <g class="growth-chart">
    <rect class="bar--light" x="258" y="724" width="52" height="41"/>
    <rect class="bar--mid" x="316" y="721" width="52" height="44"/>
    <rect class="bar--light" x="373" y="696" width="52" height="69"/>
    <rect class="bar--light" x="431" y="678" width="52" height="87"/>
    <rect class="bar--dark" x="488" y="620" width="52" height="145"/>
    <line class="chart-axis" x1="237" y1="765" x2="564" y2="765"/>
    <path class="trend-line" d="M253,684 Q420,690 520,566"/>
    <path class="trend-head" d="M538,540 L540,580 L526,566 L498,558 Z"/>
  </g>
</svg>
</body>
</html>
```